cleaning service

we are a cleaning company,

we have a current flyer but its very dull

I have attached it, can we make it look modern, maybe add pictures and colour

```html
<!DOCTYPE html>
<html lang="en">
<head>
<meta charset="utf-8">
<title>Carpet Cleaning – Maple Lane Cleaning Services</title>
<link href="https://fonts.googleapis.com/css2?family=Roboto+Condensed:wght@400;500;700&family=Inter:wght@300;400&display=swap" rel="stylesheet">
<style>
  :root{
    --red:#9b1c1f;
    --ink:#141414;
    --cream:#fdf2df;
    --cream-light:#fffdf9;
    --yellow:#fdc814;
    --orange:#fbab18;
    --row:#fdefd8;
    --row-edge:#fbe4bb;
  }
  *{margin:0;padding:0;box-sizing:border-box}
  html,body{width:850px;height:1200px;overflow:hidden}
  body{font-family:"Inter",Helvetica,Arial,sans-serif;color:var(--ink)}
  .flyer{
    position:relative;width:850px;height:1200px;overflow:hidden;
    background:linear-gradient(180deg,#ffffff 0%,var(--cream-light) 18%,var(--cream) 70%,#fdf0da 100%);
  }
  .blob{position:absolute}
  .blob-top{top:0;right:0;width:234px;height:160px}
  .blob-bottom{left:0;bottom:0;width:272px;height:178px}
  .cleaner-figure{
    position:absolute;left:662px;top:20px;width:124px;height:150px;
    background:linear-gradient(180deg,#e9eef4 0%,#4a7fb8 45%,#2f5f96 100%);
    border-radius:40px 40px 8px 8px;opacity:.9;
  }
  .brand{position:absolute;left:85px;top:57px;font-family:"Roboto Condensed",Arial Narrow,sans-serif;font-weight:700;font-size:20px;line-height:25px;letter-spacing:.2px}
  .brand .name{color:var(--red)}
  .service-icon{
    position:absolute;left:84px;top:274px;width:103px;height:103px;border-radius:50%;
    border:1.3px solid var(--red);display:flex;align-items:center;justify-content:center;
  }
  .service-icon .icon-fill{width:56px;height:44px;background:var(--red);border-radius:10px 10px 4px 4px}
  .backdrop-art{
    position:absolute;left:430px;top:252px;width:328px;height:180px;
    background:linear-gradient(180deg,#faeee3,#f7e6d6);border-radius:60px 60px 16px 16px;opacity:.55;
  }
  .title{position:absolute;left:85px;top:397px;font-family:"Roboto Condensed",Arial Narrow,sans-serif;font-weight:700;font-size:26.5px;color:var(--red)}
  .intro{
    position:absolute;left:85px;top:452px;width:692px;column-count:2;column-gap:44px;
    font-size:16.2px;line-height:22.8px;font-weight:300;letter-spacing:-0.25px;color:#1a1a1a;height:184px;
  }
  .price-panel{
    position:absolute;left:81px;top:660px;width:688px;height:231px;border-radius:0 0 14px 14px;
    background:linear-gradient(180deg,rgba(253,239,214,0) 0%,#fde9c0 60%,#fde1a8 100%);
  }
  .price-list{position:absolute;left:137px;top:682px;width:576px;list-style:none}
  .price-list li{
    height:26.7px;margin-bottom:2px;background:var(--row);border-bottom:2px solid var(--row-edge);
    display:flex;align-items:flex-end;font-family:"Roboto Condensed",Arial Narrow,sans-serif;
  }
  .price-list .item{width:457px;padding-left:15px;font-size:17px;font-weight:500;padding-bottom:1px}
  .price-list .price{font-size:25px;font-weight:700;color:var(--red);line-height:26px}
  .price-list .unit{font-size:15.5px;font-weight:500;color:var(--ink);margin-left:4px;padding-bottom:1px}
  .footnote{position:absolute;left:83px;top:907px;width:700px;font-size:13.6px;line-height:17px;font-weight:400}
  .call-bar{
    position:absolute;left:383px;top:1082px;width:467px;height:60px;border-radius:22px 0 0 22px;
    background:linear-gradient(180deg,#fffaf0 0%,#fde9bf 60%,#fcd27c 100%);
    border-top:1.5px solid #f9c561;
    padding:14px 0 0 32px;font-family:"Roboto Condensed",Arial Narrow,sans-serif;font-weight:700;
  }
  .call-bar .turn{font-size:11.5px;line-height:13px}
  .call-bar .phone{font-size:20.3px;line-height:25px;color:var(--red)}
</style>
</head>
<body>
<div class="flyer">
  <svg class="blob blob-top" viewBox="0 0 234 160" aria-hidden="true">
    <defs><linearGradient id="gt" x1="0" y1="0" x2="1" y2="0"><stop offset="0" stop-color="#fbb318"/><stop offset="1" stop-color="#fdcc14"/></linearGradient></defs>
    <path d="M0 0 C10 30 40 55 85 58 C140 62 165 70 185 105 C200 135 215 155 234 158 L234 0 Z" fill="url(#gt)"/>
  </svg>
  <div class="cleaner-figure" role="img" aria-label="Illustration of a cleaner in blue overalls sweeping with a broom"></div>

  <div class="brand">CLEANING SERVICES<br>by <span class="name">MAPLE LANE</span></div>

  <div class="backdrop-art" role="img" aria-label="Faint large vacuum cleaner decoration"></div>
  <div class="service-icon"><div class="icon-fill" role="img" aria-label="Vacuum cleaner on a sparkling carpet icon"></div></div>

  <h1 class="title">Carpet Cleaning</h1>
  <p class="intro">Maple Lane Cleaning services provides professional carpet cleaning service, carried out by our certified cleaners with years of professional experience. Our reputation speaks for itself.<br>We provide a high-quality deep carpet cleaning service for all types of rugs and carpets. The method we apply when tending to the textile floorings is hot water extraction, also known as steam cleaning. We also do stain removal, treating even old stubborn spots and spills on all types of rugs. With us, you can also add Tuftwell stain protection service to enhance the results of the deep carpet cleaning.</p>

  <div class="price-panel"></div>
  <ul class="price-list">
    <li><span class="item">Single Bedroom</span><span class="price">£19</span></li>
    <li><span class="item">Double Bedroom</span><span class="price">£24</span></li>
    <li><span class="item">Living / Dining / Lounge</span><span class="price">£29</span></li>
    <li><span class="item">Hallway</span><span class="price">£13</span></li>
    <li><span class="item">Landing</span><span class="price">£7</span></li>
    <li><span class="item">Steps</span><span class="price">£2</span><span class="unit">( per step )</span></li>
    <li><span class="item">Bathroom</span><span class="price">£6</span></li>
  </ul>

  <p class="footnote">* All Cleaning Materials and Equipment are included in the price. Minimum charge of £49 applies for carpet and upholstery cleaning services.</p>

  <svg class="blob blob-bottom" viewBox="0 0 272 178" aria-hidden="true">
    <defs><linearGradient id="gb" x1="0" y1="0" x2="1" y2="1"><stop offset="0" stop-color="#fdce14"/><stop offset="1" stop-color="#fbaa18"/></linearGradient></defs>
    <path d="M0 0 C20 10 25 50 28 80 C32 110 70 105 110 112 C150 120 140 150 200 160 C240 166 262 170 272 178 L0 178 Z" fill="url(#gb)"/>
  </svg>

  <div class="call-bar">
    <div class="turn">Please turnover for our services and prices</div>
    <div class="phone">Please call us on 07700900123 to beat any price</div>
  </div>
</div>
</body>
</html>
```